"Harbor Builders" is a residential building company and needs a new business card design and may re

We would like a redesign based on the existing logo, and would like to see a new font as well. We are bespoke home builders who build sustainable energy efficient homes.

Industry/Entity Type

Construction

Contact Information for Business Card

Business card size 40mm x 90mm

Colors

Designer to choose colors to be used in the design.

```html
<!DOCTYPE html>
<html lang="en">
<head>
<meta charset="utf-8">
<title>Harbor Builders – Business Card</title>
<link rel="stylesheet" href="https://fonts.googleapis.com/css2?family=Roboto:wght@400;500;700&family=Roboto+Condensed:wght@700&display=swap">
<style>
  :root {
    --backdrop: #5b4838;
    --card-white: #f1f1f1;
    --ink: #060708;
    --text-grey: #4a4a4a;
    --lime: #b5c92e;
    --divider: #9a9a9a;
  }
  * { margin: 0; padding: 0; box-sizing: border-box; }
  html, body { width: 1200px; height: 960px; overflow: hidden; }
  body {
    background: var(--backdrop);
    position: relative;
    font-family: "Roboto", Arial, sans-serif;
  }
  .card {
    position: absolute;
    width: 600px;
    height: 343px;
    overflow: hidden;
  }
  .card-front { left: 314px; top: 113px; background: var(--card-white); }
  .card-back { left: 311px; top: 472px; }

  .card-shapes { position: absolute; inset: 0; }

  .wordmark {
    position: absolute;
    left: 36px;
    top: 150px;
    width: 240px;
    display: flex;
    align-items: center;
    gap: 10px;
    font-family: "Roboto", Arial, sans-serif;
    font-weight: 700;
    font-size: 24px;
    color: var(--ink);
    white-space: nowrap;
  }
  .wordmark-square { width: 18px; height: 18px; background: var(--lime); flex: none; }

  .divider {
    position: absolute;
    left: 296px;
    top: 72px;
    width: 1px;
    height: 205px;
    background: linear-gradient(to bottom, transparent, var(--divider) 20%, var(--divider) 80%, transparent);
  }

  .contact { position: absolute; left: 320px; top: 76px; color: var(--text-grey); font-size: 14.5px; line-height: 18.5px; }
  .contact-name {
    font-family: "Roboto Condensed", "Arial Narrow", sans-serif;
    font-weight: 700;
    font-size: 22px;
    color: var(--ink);
    margin-bottom: 10px;
    line-height: 26px;
  }
  .contact-company { font-weight: 700; }
  .contact-reg { margin-top: 2px; }
  .contact-links { list-style: none; margin-top: 5px; }
  .contact-links li { display: flex; align-items: center; gap: 9px; }
  .contact-links svg { width: 13px; height: 13px; flex: none; }

  .back-name {
    position: absolute;
    left: 0; right: 0;
    top: 140px;
    text-align: center;
    font-family: "Roboto", Arial, sans-serif;
    font-weight: 700;
    font-size: 46px;
    color: var(--card-white);
  }
  .back-url {
    position: absolute;
    left: 0; right: 0;
    top: 297px;
    text-align: center;
    font-size: 14px;
    letter-spacing: 3px;
    color: var(--card-white);
  }
</style>
</head>
<body>

<section class="card card-front" aria-label="Business card front">
  <svg class="card-shapes" viewBox="0 0 600 343" aria-hidden="true">
    <polygon points="0,301 298,334 298,343 0,343" fill="var(--ink)"/>
    <polygon points="301,334 600,301 600,343 301,343" fill="var(--lime)"/>
  </svg>

  <div class="wordmark">
    <span class="wordmark-square"></span>
    <span>Harbor Builders</span>
  </div>

  <div class="divider"></div>

  <div class="contact">
    <h1 class="contact-name">DANIEL FERRARO</h1>
    <p class="contact-company">Harbor Builders Pty Ltd</p>
    <p>PO Box 4172 Eastgate</p>
    <p>LPO Ashby WA 6065</p>
    <p class="contact-reg">Registration 40318</p>
    <p>ABN: 52 309 641 778</p>
    <ul class="contact-links">
      <li>
        <svg viewBox="0 0 13 13" aria-hidden="true"><rect x="3" y="0.5" width="7" height="12" rx="1.2" fill="none" stroke="var(--ink)" stroke-width="1.4"/><rect x="4.5" y="2.2" width="4" height="7" fill="var(--ink)"/></svg>
        <span>0400 123 987</span>
      </li>
      <li>
        <svg viewBox="0 0 13 13" aria-hidden="true"><rect x="1" y="3" width="11" height="7.5" fill="var(--ink)"/><polyline points="1,3 6.5,7.5 12,3" fill="none" stroke="var(--card-white)" stroke-width="1"/></svg>
        <span>daniel@harborbuilders.com.au</span>
      </li>
      <li>
        <svg viewBox="0 0 13 13" aria-hidden="true"><circle cx="6.5" cy="6.5" r="6" fill="var(--ink)"/><path d="M4 3.5 Q6 4.5 5 6.5 Q4 8 6 9.5 M8.5 3 Q9.5 5 8 6 Q9 8 10.5 8" fill="none" stroke="var(--card-white)" stroke-width="1.1"/></svg>
        <span>www.harborbuilders.com.au</span>
      </li>
    </ul>
  </div>
</section>

<section class="card card-back" aria-label="Business card back">
  <svg class="card-shapes" viewBox="0 0 600 343" aria-hidden="true">
    <rect x="0" y="0" width="297" height="343" fill="var(--ink)"/>
    <rect x="297" y="0" width="4" height="343" fill="var(--card-white)"/>
    <rect x="301" y="0" width="299" height="343" fill="var(--lime)"/>
  </svg>
  <p class="back-name">Harbor Builders</p>
  <p class="back-url">www.harborbuilders.com.au</p>
</section>

</body>
</html>
```